Tallowood building company Business card design

I need a business card design for my company. I have a logo but dont have business cards with our logo..

www.tallowoodbuildingco.com.au

The logo is on the website

I need the same details as this design I have attached. we have changed the logo and colours. just like the website

Building

```html
<!DOCTYPE html>
<html lang="en">
<head>
<meta charset="utf-8">
<title>Tallowood Building – Business Card</title>
<link rel="stylesheet" href="https://fonts.googleapis.com/css2?family=Libre+Baskerville&family=Lato:wght@400&display=swap">
<style>
  :root {
    --brand-blue: #138bc8;
    --band-grey: #bcbdc0;
    --rule-grey: #b5b6b8;
    --ink: #111111;
    --paper: #ffffff;
    --backdrop: #e9edf0;
  }
  * { margin: 0; padding: 0; box-sizing: border-box; }
  html, body {
    width: 1200px; height: 965px; overflow: hidden;
    background: var(--backdrop);
  }
  .business-card {
    position: absolute; left: 57px; top: 160px;
    width: 1086px; height: 644px;
    background: var(--paper);
    font-family: "Lato", Arial, sans-serif;
    color: var(--ink);
  }
  .brand-mark {
    position: absolute; left: 181px; top: 60px;
    width: 150px; height: 150px;
    background: var(--brand-blue);
  }
  .brand-name {
    position: absolute; left: 20px; top: 262px; width: 474px;
    text-align: center;
    font-family: "Libre Baskerville", Georgia, serif;
    font-weight: 400;
    color: var(--brand-blue);
    line-height: 1.1;
  }
  .brand-name .line-main { display: block; font-size: 50px; letter-spacing: 1px; }
  .brand-name .line-sub { display: block; font-size: 34px; letter-spacing: 12px; margin-top: 10px; padding-left: 12px; }
  .brand-rule {
    position: absolute; left: 40px; top: 400px;
    width: 434px; height: 2px; background: var(--rule-grey);
  }
  .tagline {
    position: absolute; left: 20px; top: 418px; width: 474px;
    text-align: center; font-size: 23px; line-height: 1.4;
  }
  .column-divider {
    position: absolute; left: 507px; top: 130px;
    width: 2px; height: 360px;
    background: linear-gradient(to bottom, rgba(180,181,184,0), var(--rule-grey) 15%, var(--rule-grey) 85%, rgba(180,181,184,0));
  }
  .person-name {
    position: absolute; left: 547px; top: 132px;
    font-family: "Libre Baskerville", Georgia, serif;
    font-variant: small-caps; font-size: 38px; letter-spacing: 1px;
  }
  .person-role {
    position: absolute; left: 682px; top: 184px;
    font-size: 29px; letter-spacing: 1px; color: var(--brand-blue);
  }
  .contact-list { position: absolute; left: 540px; top: 312px; list-style: none; }
  .contact-item {
    display: flex; align-items: center;
    height: 42px; margin-bottom: 21px; font-size: 29px;
  }
  .contact-item svg { width: 36px; height: 32px; margin-right: 24px; fill: var(--brand-blue); }
  .web-band {
    position: absolute; left: 0; top: 549px; width: 100%; height: 56px;
    background: var(--brand-blue);
    color: var(--paper); font-size: 32px;
    text-align: right; padding-right: 72px; line-height: 56px;
  }
  .base-band {
    position: absolute; left: 0; top: 605px; width: 100%; height: 39px;
    background: var(--band-grey);
  }
</style>
</head>
<body>
  <div class="business-card">
    <div class="brand-mark"></div>
    <div class="brand-name">
      <span class="line-main">TALLOWOOD</span>
      <span class="line-sub">BUILDING</span>
    </div>
    <div class="brand-rule"></div>
    <p class="tagline">New Homes, Addition &amp; Renovation<br>Domestic &amp; Commercial Builders</p>

    <div class="column-divider"></div>

    <h1 class="person-name">Marek Dorsey</h1>
    <p class="person-role">Director</p>

    <ul class="contact-list">
      <li class="contact-item">
        <svg viewBox="0 0 36 32" aria-hidden="true">
          <path d="M3 10c0-5 6-7 15-7s15 2 15 7v3h-8v-4c-2-1-5-1-7-1s-5 0-7 1v4H3z"/>
          <path d="M9 14h18l5 14H4z"/>
        </svg>
        9512 3470
      </li>
      <li class="contact-item">
        <svg viewBox="0 0 36 32" aria-hidden="true">
          <path d="M11 0h14a3 3 0 0 1 3 3v26a3 3 0 0 1-3 3H11a3 3 0 0 1-3-3V3a3 3 0 0 1 3-3zm0 4v21h14V4z"/>
        </svg>
        0422519836 (Marek)
      </li>
      <li class="contact-item">
        <svg viewBox="0 0 36 32" aria-hidden="true">
          <path d="M2 5h32v22H2zm3 3v1l13 9 13-9V8zm0 4v12h26V12L18 21z"/>
        </svg>
        info@tallowoodbuildingco.com.au
      </li>
    </ul>

    <div class="web-band">www.tallowoodbuildingco.com.au</div>
    <div class="base-band"></div>
  </div>
</body>
</html>
```